KDL Business card design

we are a new real estate agent, mainly selling off the plan projects, most of our client are overseas buyers. Please design a letter mark logo with "K D L" which is the name of the company. and the back side of the business card, i would like to have the logo on it. I was thinking to use "monoton" font for the "K D L" logo,and use "red, yellow, blue" colour in order on each letter. please give me some opinions. or design a better one for me.

Reason: I would like to reduce the deadline to 9/7/13 , thanks

Please add job title: Licensed Real Estate Agent

Industry/Entity Type

Real Estate

Contact Information for Business Card

Company Name: Bramblewood Equity Holdings Pty. Ltd. ,Name: Marcus Delane , Address: PO Box 372 Tarrawick BC NSW 2196 , mob: 0431 592 746 , Phone: 02 8365 4017 Email: marcus.delane@bramblewoodkdl.com.au

Logo styles of interest
Lettermark Logo

```html
<!DOCTYPE html>
<html lang="en">
<head>
<meta charset="utf-8">
<title>KDL Business Card</title>
<link rel="stylesheet" href="https://fonts.googleapis.com/css2?family=Montserrat:wght@400;500;600;700&display=swap">
<style>
  :root {
    --page-bg: #d9d9db;
    --card-bg: #1e1a1d;
    --card-bg-soft: #2a2529;
    --accent-red: #c8321f;
    --accent-orange: #e4572b;
    --band-red: #b3261a;
    --cream: #f2e6c9;
    --text-grey: #8c8589;
    --white: #f6f1ec;
  }
  * { box-sizing: border-box; margin: 0; padding: 0; }
  html, body {
    width: 1200px;
    height: 901px;
    overflow: hidden;
    background: var(--page-bg);
    font-family: "Montserrat", Arial, sans-serif;
  }
  .stage {
    width: 1200px;
    height: 901px;
    display: flex;
    align-items: center;
    justify-content: center;
    gap: 40px;
  }
  .card {
    position: relative;
    width: 540px;
    height: 330px;
    background: var(--card-bg);
    overflow: hidden;
    box-shadow: 0 10px 28px rgba(0,0,0,0.25);
  }

  /* Back side */
  .card-back .pattern-field {
    position: absolute;
    inset: 0;
    background: linear-gradient(135deg, var(--card-bg-soft) 0%, var(--card-bg) 70%);
  }
  .card-back .back-mark {
    position: absolute;
    right: 48px;
    top: 54px;
    font-size: 78px;
    font-weight: 500;
    letter-spacing: 6px;
    line-height: 1;
    color: var(--cream);
  }

  /* Front side */
  .front-mark {
    position: absolute;
    left: 42px;
    top: 40px;
    font-size: 76px;
    font-weight: 500;
    letter-spacing: 6px;
    line-height: 1;
    color: var(--accent-orange);
  }
  .company-name {
    position: absolute;
    left: 44px;
    top: 124px;
    font-size: 10.5px;
    font-weight: 500;
    color: var(--accent-red);
  }
  .person-name {
    position: absolute;
    left: 44px;
    top: 156px;
    font-size: 21px;
    font-weight: 600;
    color: var(--accent-red);
  }
  .contact-list {
    position: absolute;
    left: 44px;
    top: 192px;
    display: grid;
    grid-template-columns: 50px auto;
    row-gap: 4px;
    font-size: 11px;
  }
  .contact-label { color: var(--accent-red); font-weight: 600; }
  .contact-value { color: var(--text-grey); font-weight: 500; }
  .address-band {
    position: absolute;
    left: 0;
    right: 0;
    bottom: 0;
    height: 62px;
    background: var(--band-red);
    display: flex;
    align-items: center;
    padding-left: 44px;
    font-size: 12px;
    font-weight: 600;
    color: var(--white);
  }
</style>
</head>
<body>
<main class="stage">
  <section class="card card-back" aria-label="Card back">
    <div class="pattern-field" role="img" aria-label="Repeating dark tonal background pattern"></div>
    <div class="back-mark">KDL</div>
  </section>

  <section class="card card-front" aria-label="Card front">
    <div class="front-mark">KDL</div>
    <p class="company-name">Bramblewood Equity Holdings Pty. Ltd.</p>
    <h1 class="person-name">Marcus Delane</h1>
    <dl class="contact-list">
      <dt class="contact-label">Mob</dt><dd class="contact-value">0431 592 746</dd>
      <dt class="contact-label">Phone</dt><dd class="contact-value">02 8365 4017</dd>
      <dt class="contact-label">Email</dt><dd class="contact-value">marcus.delane@bramblewoodkdl.com.au</dd>
    </dl>
    <div class="address-band">PO Box 372 Tarrawick BC NSW 2196</div>
  </section>
</main>
</body>
</html>
```